Meadowrun Acres Website Design

We have been redeveloping our website already and are quite happy with the content, but the design needs to be better:
https://tilvexa-hub.examplehost.net/

Pages, content, concept etc. Can all be taken from the redeveloped website.
The farmer can register and edit/view their profile, subscribe and these pages need to be designed better as well as contact, about, pricing, tos, privacy and a page with example portlets.

We need a website to appeal to farmers, investors and retiring farmers.

The design should be clean and a little country.

We don't want any repeat designs that some may submit to every project and has no respect for the project brief, so please don't submit them.

Target Market(s)

farmers, investors, retirees

Industry/Entity Type

Farming

Number of Pages Required

5+ page

Colors

Designer to choose colors to be used in the design.

Requirements
Must have
• Nice, clean modern design that is appealing
• Profile page laid out nicely

```html
<!DOCTYPE html>
<html lang="en">
<head>
<meta charset="utf-8">
<title>Retiring Farmers | Meadowrun Acres</title>
<link href="https://fonts.googleapis.com/css2?family=Roboto:wght@300;400;500;700&family=Questrial&display=swap" rel="stylesheet">
<style>
:root{
  --green:#2e9b36;
  --green-dark:#247a2b;
  --orange:#f7810f;
  --ink:#222;
  --text:#555;
  --muted:#777;
  --line:#dcdcdc;
  --soft:#f1f1f1;
  --footer:#333;
  --footer-bar:#2a2a2a;
  --white:#fff;
}
*{box-sizing:border-box;margin:0;padding:0}
html,body{width:1200px;height:3666px;overflow:hidden}
body{position:relative;background:var(--white);font-family:'Roboto',Arial,sans-serif;color:var(--text)}
.abs{position:absolute}
.site-header{left:0;top:0;width:1200px;height:93px;background:var(--white);box-shadow:0 1px 4px rgba(0,0,0,.08);z-index:3}
.brand-badge{left:62px;top:4px;width:124px;height:124px;border-radius:50%;background:var(--white);z-index:4;display:flex;flex-direction:column;align-items:center;justify-content:center;gap:6px;box-shadow:0 2px 6px rgba(0,0,0,.12)}
.brand-badge .dot{width:26px;height:26px;border-radius:50%;background:var(--green)}
.brand-badge .name{font-size:13px;font-weight:700;color:var(--green);text-align:center;line-height:1.15}
.main-nav{left:225px;top:37px;display:flex;gap:33px;font-size:14.5px;font-weight:700;text-transform:uppercase;color:var(--ink)}
.main-nav a{color:inherit;text-decoration:none}
.main-nav .active{color:var(--green);border-bottom:3px solid var(--green);padding-bottom:6px}
.account-link{left:950px;top:37px;font-size:14.5px;font-weight:700;color:var(--orange);text-transform:uppercase;display:flex;align-items:center;gap:10px}
.hero{left:0;top:93px;width:1200px;height:254px;background:linear-gradient(90deg,#5a6a45 0%,#7d8c5c 30%,#6d7b8e 55%,#8aa070 80%,#5d6f44 100%)}
.hero-title{left:0;top:195px;width:1200px;text-align:center;font-size:40px;font-weight:700;color:var(--white);text-shadow:0 2px 6px rgba(0,0,0,.4)}
.breadcrumb{left:0;top:347px;width:1200px;height:44px;background:var(--soft);padding:12px 73px;font-size:14px;color:var(--ink)}
.breadcrumb span{color:var(--green)}
.intro-card{left:73px;top:440px;width:509px;height:332px;border:8px solid var(--green);padding:30px 28px;text-align:center;font-size:18px;line-height:1.45;color:var(--ink);box-shadow:0 0 0 2px #d6ead7 inset}
.intro-card .accent{color:var(--green)}
.btn{display:inline-block;background:var(--orange);color:var(--white);font-weight:700;text-transform:uppercase;text-align:center;border-radius:3px}
.intro-card .btn{position:absolute;left:22px;right:22px;bottom:24px;height:44px;line-height:44px;font-size:19px}
.video-frame{left:611px;top:440px;width:513px;height:332px;border:8px solid var(--green);border-left:none;border-bottom:none}
.video-area{left:611px;top:448px;width:505px;height:324px;background:linear-gradient(135deg,#4a4838,#6b6a50 45%,#3d3e33)}
.play{left:833px;top:582px;width:62px;height:52px;border-radius:50%;background:rgba(0,0,0,.55)}
.copy{left:73px;top:814px;width:1052px;font-size:14px;line-height:1.6;color:var(--text)}
.copy p{margin-bottom:22px}
.banner{left:0;top:1088px;width:1200px;height:496px;background:linear-gradient(180deg,#6b6f68 0%,#5d6a4c 45%,#6e7d3f 75%,#55612e 100%)}
.banner-title{left:0;top:1258px;width:1200px;text-align:center;font-family:'Questrial',Arial,sans-serif;font-size:66px;line-height:1.05;color:var(--white)}
.section-title{left:0;width:1200px;text-align:center;font-size:26px;font-weight:500;color:var(--ink)}
.spine{left:599px;top:1730px;width:4px;height:770px;background:var(--soft)}
.node{width:84px;height:84px;border-radius:50%;background:var(--white);border:2px solid var(--line);display:flex;align-items:center;justify-content:center;left:559px}
.benefit{width:466px}
.benefit h3{font-size:19px;font-weight:700;color:var(--ink);margin-bottom:6px}
.benefit p{font-size:14px;color:var(--text);border-top:1px solid var(--line);padding-top:8px}
.benefit.left{left:73px;text-align:right}
.benefit.right{left:667px}
.section-btn{left:534px;width:134px;height:38px;line-height:38px;font-size:14px}
.divider{left:73px;top:2671px;width:1052px;height:1px;background:var(--line)}
.track{left:73px;top:2986px;width:1054px;height:3px;background:var(--green)}
.stop{width:116px;height:116px;border-radius:50%;background:var(--white);border:3px solid var(--green);box-shadow:0 0 0 7px var(--soft) inset;display:flex;align-items:center;justify-content:center}
.stem{width:3px;background:var(--green)}
.step{width:260px;text-align:center}
.step h3{font-size:19px;font-weight:700;color:var(--ink);margin-bottom:10px}
.step p{font-size:14px;line-height:1.55;color:var(--text)}
.site-footer{left:0;top:3326px;width:1200px;height:291px;background:var(--footer)}
.footer-heading{font-size:16px;font-weight:500;color:var(--white)}
.post{left:73px;width:340px;display:flex;gap:16px}
.post .date{width:56px;height:62px;background:var(--green);color:var(--white);text-align:center;padding-top:4px;flex-shrink:0}
.post .date b{display:block;font-size:30px;line-height:1}
.post .date small{font-size:10px;text-transform:uppercase}
.post h4{font-size:16px;font-weight:700;color:var(--white);line-height:1.3}
.post span{font-size:12px;color:#aaa}
.signup-note{left:496px;top:3401px;width:340px;font-size:14px;color:#bbb;line-height:1.5}
.email-field{left:496px;top:3456px;width:332px;height:38px;border-radius:19px;background:var(--white);padding:10px 18px;font-size:14px;color:#999}
.subscribe{left:496px;top:3503px;width:130px;height:38px;line-height:38px;border-radius:19px;font-size:15px;text-transform:none}
.footer-brand{left:880px;top:3380px;width:240px;display:flex;flex-direction:column;align-items:center;gap:16px}
.footer-brand .dot{width:60px;height:60px;border-radius:50%;border:3px solid #ccc}
.footer-brand .name{font-size:24px;color:#ccc}
.footer-bar{left:0;top:3617px;width:1200px;height:49px;background:var(--footer-bar);padding:16px 73px;font-size:12px;color:#aaa}
.social{top:3627px;width:30px;height:30px;border-radius:50%;background:#aaa}
</style>
</head>
<body>

<header class="abs site-header">
  <nav class="abs main-nav">
    <a class="active">Home</a><a>Aspiring Farmers</a><a>Investors</a><a>Retiring Farmer</a><a>Blog</a><a>Pricing</a><a>Contact</a>
  </nav>
  <div class="abs account-link">
    <svg width="16" height="16" viewBox="0 0 16 16"><path d="M6 2H2v12h4M6 8h8M11 5l3 3-3 3" fill="none" stroke="#f7810f" stroke-width="2"/></svg>
    Sign in or sign up
  </div>
</header>
<div class="abs brand-badge"><span class="dot"></span><span class="name">Meadowrun<br>Acres</span></div>

<div class="abs hero" role="img" aria-label="Photo of a farming family with a young farmer and small children outdoors"></div>
<h1 class="abs hero-title">Retiring Farmers</h1>
<div class="abs breadcrumb"><span>Home</span> / Retiring Farmers</div>

<div class="abs intro-card">
  Are you looking for a positive way to step back from your farm?<br>
  We can connect you with a passionate aspiring farming family who will love your farm just as much as you do. No registration required and your information will be kept private<br>
  <span class="accent">Get in touch discuss the best farm succession opportunity for you</span>
  <span class="btn">Enquire now</span>
</div>
<div class="abs video-frame"></div>
<div class="abs video-area" role="img" aria-label="Video still of a young farmer speaking outdoors"></div>
<svg class="abs play" viewBox="0 0 62 52"><path d="M24 15l18 11-18 11z" fill="#fff"/></svg>

<div class="abs copy">
  <p>We provide an alternative succession option which is a win-win for you and your community.</p>
  <p>You can retain ownership, provide mentoring to the new family and ensure your community thrives because you are fostering the next generation of farmers.</p>
  <p>We connect you with young passionate farmers who will love your farm as much as you do. There are many different ways that you can transition off your farm as you enter retirement.</p>
  <p>You don't have to sell and walk away. We can help find an aspiring farmer who can purchase some equity and manage the farm, which allows you to step back and become the Chairperson rather than the CEO. Get in touch with us and we would be happy to discuss different ways that you can support a new farming family, grow your farm and support your local community.</p>
</div>

<div class="abs banner" role="img" aria-label="Photo of a stockman on horseback herding cattle past a farm shed"></div>
<h2 class="abs banner-title">Find Your Dream Transition<br>With Us</h2>

<h2 class="abs section-title" style="top:1632px">Benefits</h2>
<div class="abs spine"></div>

<div class="abs benefit left" style="top:1741px"><h3>Succession</h3><p>A new farm succession option</p></div>
<div class="abs node" style="top:1729px"><svg width="40" height="40" viewBox="0 0 40 40" fill="none" stroke="#2e9b36" stroke-width="3.5"><path d="M6 14h26M26 8l6 6-6 6M34 27H8M14 21l-6 6 6 6"/></svg></div>

<div class="abs benefit right" style="top:1843px"><h3>Equity</h3><p>Retain equity in your farm - you don't have to sell up completely</p></div>
<div class="abs node" style="top:1832px"><svg width="40" height="40" viewBox="0 0 40 40" fill="#2e9b36"><path d="M20 4l15 8-15 8-15-8z"/><path d="M4 15l14 8v15L4 30zM36 15l-14 8v15l14-8z"/></svg></div>

<div class="abs benefit left" style="top:1946px"><h3>Return</h3><p>Continue to receive an income from your farm</p></div>
<div class="abs node" style="top:1935px"><svg width="40" height="40" viewBox="0 0 40 40" fill="none" stroke="#2e9b36" stroke-width="3.5"><path d="M5 5v30h30M10 28l8-9 6 5 10-12"/></svg></div>

<div class="abs benefit right" style="top:2049px"><h3>Capital</h3><p>Realise capital returns if you exit completely in the future</p></div>
<div class="abs node" style="top:2038px"><svg width="40" height="40" viewBox="0 0 40 40" fill="#2e9b36"><path d="M18 6a15 15 0 1 0 15 17H18z"/><path d="M22 3v16h15A16 16 0 0 0 22 3z"/></svg></div>

<div class="abs benefit left" style="top:2151px"><h3>Community</h3><p>Stay and support your community</p></div>
<div class="abs node" style="top:2140px"><svg width="44" height="40" viewBox="0 0 44 40" fill="#2e9b36"><circle cx="22" cy="10" r="6"/><circle cx="10" cy="15" r="5"/><circle cx="34" cy="15" r="5"/><path d="M12 34c0-9 4-14 10-14s10 5 10 14zM2 34c0-7 3-11 8-11 2 0 3 1 4 2-2 3-3 6-3 9zM42 34c0-7-3-11-8-11-2 0-3 1-4 2 2 3 3 6 3 9z"/></svg></div>

<div class="abs benefit right" style="top:2254px"><h3>Connection</h3><p>Retain your family connection to your farm</p></div>
<div class="abs node" style="top:2243px"><svg width="40" height="40" viewBox="0 0 40 40" fill="none" stroke="#2e9b36" stroke-width="4"><path d="M18 14l8 8-6 6c-3 3-8 3-10 0s-3-7 0-10zM22 8l-6 6M32 18l-6 6M10 30l-6 6"/></svg></div>

<div class="abs benefit left" style="top:2356px"><h3>Mentor</h3><p>Provide advice and mentoring to new young farming family</p></div>
<div class="abs node" style="top:2345px"><svg width="44" height="40" viewBox="0 0 44 40" fill="#2e9b36"><path d="M22 6L2 15l20 9 20-9z"/><path d="M10 21v8c0 4 6 6 12 6s12-2 12-6v-8l-12 6z"/><path d="M38 17v12" stroke="#2e9b36" stroke-width="2"/></svg></div>

<div class="abs benefit right" style="top:2458px"><h3>Anonymous</h3><p>Your farm and information will be kept private</p></div>
<div class="abs node" style="top:2447px"><svg width="36" height="40" viewBox="0 0 36 40"><path d="M10 18v-6a8 8 0 0 1 16 0v6" fill="none" stroke="#2e9b36" stroke-width="4"/><rect x="5" y="18" width="26" height="19" rx="2" fill="#2e9b36"/></svg></div>

<span class="abs btn section-btn" style="top:2590px">Enquire now</span>
<div class="abs divider"></div>

<h2 class="abs section-title" style="top:2716px">Expectations</h2>

<div class="abs step" style="left:141px;top:2786px"><h3>Share</h3><p>Provide your knowledge of the farm and operations to prepare the farm for the best future possible</p></div>
<div class="abs step" style="left:571px;top:2786px"><h3>Review &amp; Discuss</h3><p>Open your books and methods to review and discussion</p></div>
<div class="abs step" style="left:356px;top:3097px"><h3>Planning</h3><p>Participate in farm planning in order to prepare for investors and support ongoing management</p></div>
<div class="abs step" style="left:786px;top:3097px"><h3>Step Back</h3><p>Hand over the reigns to the aspiring farmer to implement the new plan</p></div>

<div class="abs stem" style="left:270px;top:2896px;height:34px"></div>
<div class="abs stem" style="left:700px;top:2896px;height:34px"></div>
<div class="abs stem" style="left:485px;top:3045px;height:40px"></div>
<div class="abs stem" style="left:915px;top:3045px;height:40px"></div>
<div class="abs track"></div>

<div class="abs stop" style="left:213px;top:2929px"><svg width="50" height="46" viewBox="0 0 50 46" fill="#2e9b36"><path d="M30 4l18 16-18 16V26C18 26 9 30 3 42 5 24 14 15 30 13z"/></svg></div>
<div class="abs stop" style="left:428px;top:2929px"><svg width="40" height="52" viewBox="0 0 40 52" fill="none" stroke="#2e9b36" stroke-width="3.5"><path d="M13 36c0-6-9-10-9-19a16 16 0 0 1 32 0c0 9-9 13-9 19z"/><path d="M14 42h12M16 48h8M20 36V22"/></svg></div>
<div class="abs stop" style="left:643px;top:2929px"><svg width="54" height="46" viewBox="0 0 54 46" fill="#2e9b36"><path d="M22 2c11 0 20 7 20 15s-9 15-20 15c-2 0-4 0-6-1L6 36l3-8C5 25 2 21 2 17 2 9 11 2 22 2z"/><path d="M44 14c5 3 8 7 8 11 0 4-2 7-6 10l2 7-8-5c-2 1-4 1-6 1-6 0-11-2-14-6 14 0 24-8 24-18z"/></svg></div>
<div class="abs stop" style="left:858px;top:2929px"><svg width="50" height="46" viewBox="0 0 50 46" fill="#2e9b36"><rect x="6" y="4" width="12" height="10" rx="2"/><rect x="32" y="4" width="12" height="10" rx="2"/><path d="M4 16h18v22a6 6 0 0 1-6 6H8a6 6 0 0 1-6-6zM28 16h18l2 22a6 6 0 0 1-6 6h-8a6 6 0 0 1-6-6z"/><rect x="21" y="18" width="8" height="12"/></svg></div>

<span class="abs btn section-btn" style="top:3231px">Enquire now</span>

<footer class="abs site-footer"></footer>
<div class="abs footer-heading" style="left:73px;top:3362px">From The Blog</div>
<div class="abs post" style="top:3404px"><div class="date"><b>24</b><small>Apr 17</small></div><div><h4>Out of the Griddle Nook into the fire of soil health | Dana Pruett</h4><span>Posted by Dana Pruett</span></div></div>
<div class="abs post" style="top:3502px"><div class="date"><b>21</b><small>Apr 17</small></div><div><h4>Rowan is a fine name, so is Tilly, but their passion for farming</h4><span>Posted by Rowan and Tilly</span></div></div>
<div class="abs footer-heading" style="left:496px;top:3362px">Subscribe To Our Newsletter</div>
<div class="abs signup-note">Want to be the first to know about our amazing discount offer?</div>
<div class="abs email-field">Email Address</div>
<span class="abs btn subscribe">Subscribe</span>
<div class="abs footer-brand"><span class="dot"></span><span class="name">Meadowrun Acres</span></div>

<div class="abs footer-bar">©2017 Meadowrun Acres. Terms of Use | Privacy | Sitemap | Donate</div>
<span class="abs social" style="left:1022px"></span>
<span class="abs social" style="left:1060px"></span>
<span class="abs social" style="left:1098px"></span>

</body>
</html>
```